****Business Card Design for Quarrystone Development. Design based around attached logo/company name

I’m looking for business card design for my company Quarrystone Development Group,LLC. Design should be professional, sharp and minimal. Outside of the attached logos, greyscale colors for remainder of cards. My thoughts are two-sided card with attached logo on one side and my info on the other but open to one-sided as well with right design.
Target Market(s)
Real estate professionals including banks, private investors, property owners, developers, commercial tenants like Brewlantern, Grovika or Tanquist’s.
Industry/Entity Type
Commercial real estate development and investments.
Contact Information for Business Card
Name, title, email, phone #’s, web address and physical address
Font styles to use
Other font styles liked:
- Helvetica, Garamond, etc
Colors
Designer to choose only greyscale colors for use in the design.
Requirements
Must have
- Attached logo first or second options.
Nice to have
- Two sided card with logo on one side. Attached Logo/company name can be laid out any way that flows as long as it’s legible.name
Should not have
- No loud colors. ***Please do not include logo, I have removed the company design with a logo image.

```html
<!DOCTYPE html>
<html lang="en">
<head>
<meta charset="utf-8">
<title>Quarrystone Development Group, LLC — Business Card</title>
<link rel="stylesheet" href="https://fonts.googleapis.com/css2?family=Cinzel:wght@400&family=Tinos:wght@400&display=swap">
<style>
  :root {
    --backdrop: #2a2a2b;
    --card: #1d1d1f;
    --card-edge: #232325;
    --wordmark: #6e7078;
    --text-strong: #8d8e94;
    --text-soft: #7c7d83;
  }
  * { box-sizing: border-box; margin: 0; padding: 0; }
  html, body {
    width: 1200px;
    height: 1138px;
    overflow: hidden;
    background: var(--backdrop);
  }
  .sheet { position: relative; width: 1200px; height: 1138px; }
  .card {
    position: absolute;
    border-radius: 16px;
    overflow: hidden;
    background: linear-gradient(160deg, var(--card-edge), var(--card));
  }
  .card--front { left: 273px; top: 183px; width: 622px; height: 377px; }
  .card--back  { left: 274px; top: 606px; width: 619px; height: 376px; }

  .wordmark {
    font-family: "Cinzel", serif;
    font-weight: 400;
    color: var(--wordmark);
    line-height: 1;
  }
  .wordmark__name,
  .wordmark__sub {
    display: block;
    white-space: nowrap;
    text-align: justify;
    text-align-last: justify;
  }
  .wordmark__name { font-size: 40px; letter-spacing: 0.5px; }
  .wordmark__sub  { font-size: 14px; letter-spacing: 2px; }

  .card--front .wordmark { position: absolute; left: 45px; top: 114px; width: 300px; }
  .card--front .wordmark__sub { margin-top: 8px; }

  .card--back .wordmark {
    position: absolute;
    left: 504px;
    top: 44px;
    height: 292px;
    writing-mode: vertical-rl;
    transform: rotate(180deg);
  }
  .card--back .wordmark__name { font-size: 38px; }
  .card--back .wordmark__sub  { font-size: 14px; margin-right: 10px; }

  .person { position: absolute; left: 42px; top: 56px; }
  .person__name {
    font-family: "Cinzel", serif;
    font-size: 24px;
    color: var(--text-strong);
    letter-spacing: 0.5px;
  }
  .person__title {
    font-family: "Tinos", serif;
    font-size: 16px;
    color: var(--text-soft);
    margin-top: 2px;
  }

  .contact {
    position: absolute;
    left: 42px;
    top: 204px;
    font-family: "Tinos", serif;
    font-size: 16px;
    color: var(--text-soft);
  }
  .contact__address { line-height: 22px; margin-bottom: 10px; }
  .contact__list { list-style: none; }
  .contact__item { display: flex; align-items: center; height: 22.5px; }
  .contact__icon { width: 13px; height: 13px; margin: 0 18px 0 2px; fill: var(--text-soft); }
</style>
</head>
<body>
<main class="sheet">
  <section class="card card--front" aria-label="Card front">
    <div class="wordmark">
      <span class="wordmark__name">QUARRYSTONE</span>
      <span class="wordmark__sub">DEVELOPMENT GROUP, LLC</span>
    </div>
  </section>

  <section class="card card--back" aria-label="Card back">
    <div class="person">
      <p class="person__name">ELIAS MARR HOLLEN</p>
      <p class="person__title">Managing Director</p>
    </div>

    <div class="contact">
      <p class="contact__address">418 Ledger Row, Harlow City,<br>Fenmore, US 204518</p>
      <ul class="contact__list">
        <li class="contact__item">
          <svg class="contact__icon" viewBox="0 0 16 16" aria-hidden="true"><path d="M2 6c0-2 3-3 6-3s6 1 6 3v1h-3V6H5v1H2zM4 8h8l2 5H2z"/></svg>
          828-555-0142
        </li>
        <li class="contact__item">
          <svg class="contact__icon" viewBox="0 0 16 16" aria-hidden="true"><path d="M1 3h14v10H1zM2.5 4.5 8 9l5.5-4.5v1L8 10 2.5 5.5z" fill-rule="evenodd"/></svg>
          elias@quarrystonedev.com
        </li>
        <li class="contact__item">
          <svg class="contact__icon" viewBox="0 0 16 16" aria-hidden="true"><path d="M8 1a7 7 0 1 0 0 14A7 7 0 0 0 8 1zm0 1.3c.9 0 1.9 1.8 2.1 4.2H5.9C6.1 4.1 7.1 2.3 8 2.3zM2.4 7.5h2.2c0 .4 0 .7.1 1H2.4zm3.5 1h4.2c-.2 2.4-1.2 4.2-2.1 4.2S6.1 10.9 5.9 8.5zm5.5 0h2.2v-1h-2.2z"/></svg>
          www.quarrystonedev.com
        </li>
      </ul>
    </div>

    <div class="wordmark">
      <span class="wordmark__name">QUARRYSTONE</span>
      <span class="wordmark__sub">DEVELOPMENT GROUP, LLC</span>
    </div>
  </section>
</main>
</body>
</html>
```